Magazine Template for National Charity

We need a magazine design for an Australian youth charity called Rhythm Crews Lifting FUtures (RCLF). We engage young people through street culture music, dance and mentoring programs, and help them to turn their lives around. Our charity's vision is to see every young person have someone who believes in them and the opportunity to live their potential.

The design should have places for images of our young people during programs(we've only provided a few for you), room for quotes from young people and supporters etc, and each double spread could be a snapshot of a different program.

We will need a design template that will allow us to add all the contents for the magazine, including a contents page, report from our Chairman (1 page), letter from CEO (1 page), and following achievements of our programs including 1. RCLF Camps (2 x double spread, total 4 pages), 2. Groove Labs (2 x double spread, total 4 pages) and 3. Mentoring (2 x double spread, total 4 pages). An audited financial report of 4 pages will be copied in after our program reports, and on the back of the magazine, we'll need space for all our supporter logos. I'd also like to include a short story or case-study about young people's transformation on each program page.

We need something that's got a bit of a street edge, to keep our youthful brand, but helps us to highlight our excellence as an innovative and cutting edge charity. The final design should be emotional, eye-catching, reflective of our creative spark, and inspiring. We currently have a brand that uses a fair bit of black & white with highlights of colour, however I dont want this to limit your creativity. We use a font called Octin Spraypaint Free for our logos and program names.

We would like to present our annual report as a magazine so that it is something that people will want to pick up and look at.

Target Market(s)

This is for general public and supporters, however we'd like to use our brand instead of a professional style for this report

Industry/Entity Type

Financial

Requirements
Must have
• See notes in task description - thank you!

We will give you a few images to use as a guide however we'd love to be able to play around with the images once we have a template (we'll add different ones and change pictures around to suit the program pages). We're providing these images so that you can get a feel for our culture and be inspired to put together the template, dont worry if you use the same photos more than once on the different pages to show as an example.
Nice to have
• We already have our charity logo, however we'd love to call this RCLF Mag, RCLF Magazine or Newest RCLF Rhythmania. We'd like it to replicate a real magazine, with colour and lots of interesting sections for information & stories, rather than a boring traditional annual report template.
Should not have
• We want this magazine to stand out, and we dont want a half-hearted charity design or a polished corporate style magazine.

We want to remain bold and contemporary, and on the commercial side with a street edge - have lots of fun & thank you so much - we're very excited!

```html
<!DOCTYPE html>
<html lang="en">
<head>
<meta charset="utf-8">
<title>RCLF Mag – Mentoring Spread</title>
<link rel="stylesheet" href="https://fonts.googleapis.com/css2?family=Teko:wght@400;500&family=PT+Sans:wght@400;700&display=swap">
<style>
  :root {
    --ink: #0d0d0d;
    --paper: #ffffff;
    --lime: #8fd12a;
    --body-ink: #1e1e1e;
    --photo-black: #0b0b0b;
    --photo-dark: #1c1c1c;
    --photo-mid: #454545;
    --photo-light: #8a8a8a;
    --photo-glow: #b4b4b4;
  }
  * { box-sizing: border-box; margin: 0; padding: 0; }
  html, body { width: 1200px; height: 855px; overflow: hidden; background: var(--ink); }
  .spread {
    position: relative;
    width: 1200px;
    height: 855px;
    overflow: hidden;
    background: var(--ink);
    font-family: "PT Sans", sans-serif;
  }
  .spread__photo {
    position: absolute;
    inset: 0;
    background:
      radial-gradient(ellipse 150px 120px at 360px 470px, rgba(180,180,180,0.55), transparent 75%),
      radial-gradient(ellipse 230px 260px at 420px 600px, rgba(70,70,70,0.8), transparent 80%),
      radial-gradient(ellipse 190px 170px at 430px 230px, var(--photo-black), transparent 85%),
      radial-gradient(ellipse 340px 240px at 180px 200px, var(--photo-glow), transparent 78%),
      radial-gradient(ellipse 300px 420px at 120px 520px, var(--photo-mid), transparent 80%),
      linear-gradient(90deg, var(--photo-light) 0%, var(--photo-mid) 30%, var(--photo-dark) 55%, var(--photo-black) 70%, var(--photo-black) 100%);
  }
  .section-badge {
    position: absolute;
    left: 48px;
    top: 40px;
    width: 118px;
    height: 118px;
    border-radius: 50%;
    background: var(--lime);
    display: flex;
    align-items: center;
    justify-content: center;
    text-align: center;
    color: var(--paper);
    font-family: "Teko", sans-serif;
    font-weight: 400;
    font-size: 19px;
    line-height: 1.05;
    letter-spacing: 1.5px;
    transform: rotate(-12deg);
  }
  .brand-tag {
    position: absolute;
    right: 52px;
    top: 12px;
    width: 134px;
    height: 37px;
    background: var(--paper);
    border-radius: 0 0 8px 8px;
    display: flex;
    align-items: center;
    gap: 5px;
    padding: 2px 6px 0;
    color: var(--ink);
    font-family: "Teko", sans-serif;
    font-weight: 500;
    font-size: 15px;
    line-height: 0.85;
    letter-spacing: 0.3px;
  }
  .brand-tag__mark {
    flex: none;
    width: 8px;
    height: 8px;
    background: var(--ink);
  }
  .pull-quote {
    position: absolute;
    right: 50px;
    top: 86px;
    width: 500px;
    text-align: right;
    color: var(--lime);
    font-family: "Teko", sans-serif;
    font-weight: 400;
    font-size: 74px;
    line-height: 75px;
    letter-spacing: 3px;
  }
  .story {
    position: absolute;
    left: 632px;
    top: 527px;
    width: 514px;
    height: 276px;
    background: var(--paper);
    padding: 8px 14px 10px 12px;
    column-count: 3;
    column-gap: 14px;
    column-fill: auto;
    color: var(--body-ink);
    font-size: 9.8px;
    line-height: 1.4;
  }
  .story p { margin-bottom: 11px; }
  .folio {
    position: absolute;
    bottom: 15px;
    height: 24px;
    display: flex;
    align-items: center;
    gap: 8px;
    color: var(--paper);
    font-size: 12px;
  }
  .folio--left { left: 48px; }
  .folio--right { right: 48px; }
  .folio__num {
    display: inline-flex;
    align-items: center;
    justify-content: center;
    width: 21px;
    height: 24px;
    background: var(--lime);
    color: var(--paper);
    font-size: 14px;
    font-weight: 700;
  }
</style>
</head>
<body>
  <main class="spread">
    <div class="spread__photo" role="img" aria-label="Black and white photo of a young performer in a beanie reading handwritten lyrics from sheets of paper during a mentoring session"></div>

    <div class="section-badge">RCLF<br>MENTORING</div>

    <div class="brand-tag">
      <span class="brand-tag__mark"></span>
      <span>RHYTHM CREWS<br>LIFTING FUTURES</span>
    </div>

    <h1 class="pull-quote">“I FOUND MY<br>OWN VOICE IN<br>EVERY VERSE”</h1>

    <article class="story">
      <p>When Jordan first joined our mentoring program he kept his hood up, his headphones on and his head down. He rarely spoke, and most weeks he left before the session ended.</p>
      <p>His mentor, a local hip hop artist, never pushed. Instead he shared his own notebooks full of rough lyrics and asked Jordan what he thought. Slowly the conversations grew longer and the headphones came off.</p>
      <p>Within a few weeks Jordan was bringing his own pages, folded and creased from his pocket. The words were raw and honest, full of stories about home, school and the streets he grew up on. Together they worked line by line, shaping verses with rhythm and real weight.</p>
      <p>His confidence grew week by week. He began turning up early, helping younger crew members set up gear and listening closely before offering ideas. By the end of the program he had recorded his first track in the studio.</p>
      <p>Jordan says the program gave him something he never had before: an adult who believed in him and kept showing up, no matter how tough the week had been.</p>
      <p>He has since enrolled in a music course and hopes to mentor others one day. His mentor says the change is huge, from the way he speaks to the way he carries himself.</p>
      <p>This is what mentoring is about. One steady relationship can open doors, build trust and help a young person see a future worth working for.</p>
    </article>

    <footer>
      <div class="folio folio--left"><span class="folio__num">12</span><span>engage, inspire, educate &amp; empower</span></div>
      <div class="folio folio--right"><span>www.rclfmag.org.au</span><span class="folio__num">13</span></div>
    </footer>
  </main>
</body>
</html>
```